2-Page Flyer for the Information Session about the Quiet Pathfinder Course

This is a flyer to announce/advertise an evening Information Session about the Quiet Pathfinder Course. This Program aims at mindfully rethinking and redesigning work (and life) for people who feel stuck or not entirely satisfied with their work and/or life (please see draft flyer attached for more details). This Program is property of Bright Meadow, a company that uses a combination of Mindfulness, Design, and Entrepreneurship to help people achieve greater happiness (in their work and lives).

Target Market(s)

People who feel stuck or not entirely satisfied with their work and/or life (please see draft flyer attached for more details)

Font styles to use
Serif
Sans Serif

Colors
ffffff
f37122
33a6d7
acd037

Requirements
Must have
• All of what I will say below is suggestive (I’m not a design expert), and I’m open to divert from it, if it makes sense and feels more interesting.
• I thought initially of a 2-page flyer (please see draft flyer attached). The first page could help people grasp the essence of the event quickly (in 1 or 2 minutes), and then, if they are interested/motivated, they would continue reading through page 2, which has more info about the Program in itself.
• Potential Structure
• Page 1
• . About the Information Session on the Quiet Pathfinder Course
• . Visible Date & Time, Contacts, Venue (and other relevant info)
• . About me (the facilitator)
• Page 2
• . About the Quiet Pathfinder Course
• I include a Powerpoint draft of the flyer with the content. The design is rudimentary and precarious from an aesthetics/organization point of view, and this is mainly where I need help (and maybe in other aspects too!).
• On the flyer, I would like to include:
• . A photo of myself (I attach 1 picture).
• . 1 or 2 beautiful-nature photos (cropped or full). One may have to do with looking at the sky, dreaming, and imagining a new work and life (2 photos with sky and clouds attached). The other has to do with walking the transformation journey (the photo with the person walking through the forest path).
• . bright meadow logo or logos (there are two slightly different ones, that can be used for different purposes). For the first page, I would like the bright meadow logo that has "bright meadow" written on the bottom, with the saying "Stillness, Craft and Venture for Bright Meadow" beneath. This is the main logo. For the 2nd page, you can choose the logo that adapts better.
• - Where it says the "the way out is in" it would be great to have a similar font to the one I attach (see file "Font_the_way_out_is_in.png" and Ankecallig-fg.ttf
Nice to have
• In terms of colours, I would not divert much from the logo colours (and of course white and black). I would like the flyer to be quite white. Almost like fairy-tale white: the white horse, the white snow, the white of the stars, the white heaven. White could be the base colour. White means peace, tranquillity, calm contentment, a smile.
• And then use the other colours. The green of the mindfulness. The blue of the sky, the dreams. And the orange of the sun, the energy, the fire, the action. And maybe the black for text.
• Where it says the "the way out is in" it would be great to have a similar font to the one I attach (see file "Font_the_way_out_is_in".
• I would like this flyer to be a piece of art, in every possible way. Simple, beautiful, ease, light, peaceful, calm happy. Just like the Quiet Pathfinder Course and bright meadow Company that I am creating intends to be. The mission of this Program and Company is to be a designer, a painter (a Picasso) of happier and more fulfilling human lives.
• I am very much looking forward to seeing your proposal(s).

```html
<!DOCTYPE html>
<html lang="en">
<head>
<meta charset="utf-8">
<title>Quiet Pathfinder Course – Information Session Flyer</title>
<link href="https://fonts.googleapis.com/css2?family=Open+Sans:ital,wght@0,400;0,600;0,700;1,400;1,600&family=Oswald:wght@500;600&family=Montserrat:wght@700;800&family=Playfair+Display:ital,wght@1,700&family=Dancing+Script:wght@600&display=swap" rel="stylesheet">
<style>
:root{
  --white:#ffffff;
  --orange:#f37122;
  --blue:#33a6d7;
  --blue-deep:#1e6cc2;
  --green:#acd037;
  --ink:#2b2b2b;
  --soft-grey:#efefef;
  --mist:#e6edf2;
  --backdrop:#d9dcdf;
}
*{box-sizing:border-box;margin:0;padding:0}
html,body{width:1200px;height:878px;overflow:hidden}
body{background:var(--backdrop);font-family:"Open Sans",Arial,sans-serif;color:var(--ink);position:relative}
.page{position:absolute;top:77px;width:512px;height:724px;background:var(--white);overflow:hidden;box-shadow:0 4px 14px rgba(0,0,0,.18)}
.page--front{left:82px}
.page--back{left:606px}
.abs{position:absolute}
p{line-height:1.3}

/* brand lockup */
.brand-dot{position:absolute;border-radius:50%;background:var(--blue)}
.brand-name{position:absolute;font-family:"Open Sans",sans-serif;font-weight:400;white-space:nowrap}

/* front */
.front-tagline{left:30px;top:90px;font-size:6.6px;font-style:italic;font-weight:700;color:var(--ink);white-space:nowrap}
.title-block{left:0;top:106px;width:300px;height:156px;background:linear-gradient(90deg,var(--blue) 70%,#5db8df)}
.title{position:absolute;left:20px;font-family:"Oswald",sans-serif;font-weight:600;line-height:1;letter-spacing:.5px}
.title--quiet{top:4px;font-size:52px;color:var(--white)}
.title--path{top:62px;font-size:30px;color:var(--white)}
.title--course{top:96px;font-size:52px;color:var(--orange)}
.session-band{left:0;top:262px;width:290px;height:58px;background:linear-gradient(90deg,var(--green) 80%,rgba(172,208,55,.3))}
.session-band__label{position:absolute;left:20px;top:5px;font-family:"Playfair Display",serif;font-style:italic;font-weight:700;font-size:19px;color:var(--ink)}
.session-band__date{position:absolute;left:20px;top:34px;font-weight:700;font-size:12.2px;color:var(--ink)}
.hero-visual{left:226px;top:0;width:286px;height:352px}
.section-head{position:absolute;font-weight:700;font-size:15px;color:var(--orange)}
.body-copy{position:absolute;font-size:8.6px;color:var(--ink)}
.facilitator-zone{left:0;top:458px;width:512px;height:219px;background:var(--soft-grey);clip-path:polygon(0 6px,4% 2px,9% 7px,15% 1px,22% 6px,28% 3px,35% 8px,42% 2px,49% 6px,56% 1px,63% 7px,70% 3px,77% 8px,84% 2px,91% 6px,100% 1px,100% 100%,0 100%)}
.portrait{left:22px;top:498px;width:146px;height:146px;border-radius:50%;background:radial-gradient(circle at 50% 40%,#c9c2bb,#8a8a8c);border:3px solid var(--white)}
.facilitator-label{left:181px;top:479px;font-size:11px;font-weight:600;color:var(--ink)}
.facilitator-name{left:181px;top:493px;font-family:"Open Sans",sans-serif;font-weight:700;font-size:20px;color:var(--orange);letter-spacing:-.3px}
.facilitator-role{left:181px;top:520px;font-size:9px;font-style:italic;font-weight:600}
.facilitator-bio{left:181px;top:541px;width:313px;font-size:7.5px;text-align:justify;line-height:1.38}
.facilitator-link{left:181px;top:649px;font-size:10.5px}
.facilitator-link b{color:var(--blue)}

.footer{left:0;top:677px;width:512px;height:34px}
.footer__contact{position:absolute;left:0;top:0;width:190px;height:34px;background:var(--blue)}
.footer__booking{position:absolute;left:190px;top:0;width:322px;height:34px;background:linear-gradient(90deg,#9fc82e,var(--green))}
.footer__strip{left:0;top:711px;width:512px;height:13px;background:#111;color:var(--white);font-size:5.5px;letter-spacing:5px;padding:3px 0 0 14px}
.icon-disc{position:absolute;border-radius:50%;background:#111}
.small{font-size:6px;white-space:nowrap}
.footer-detail{font-size:5.3px;white-space:nowrap;color:#111;font-weight:600}

/* back */
.back-top{left:0;top:0;width:512px;height:73px;background:linear-gradient(180deg,#f3f4f5,#e9ebed)}
.back-band{left:0;top:73px;width:512px;height:97px;background:linear-gradient(90deg,var(--blue-deep),#3a8fd9)}
.back-band h1{position:absolute;left:25px;top:9px;font-family:"Montserrat",sans-serif;font-weight:800;font-size:25.5px;color:var(--white);white-space:nowrap}
.back-band p{position:absolute;left:24px;top:48px;width:472px;font-size:8.7px;font-style:italic;color:var(--white);text-align:justify;line-height:1.32;letter-spacing:-.1px}
.program-zone{left:0;top:170px;width:512px;height:214px;background:var(--mist)}
.program-head{left:21px;top:208px;font-weight:700;font-size:15.5px;color:#2f86c8}
.program-copy{left:21px;top:243px;width:218px;font-size:8.1px}
.cycle{left:250px;top:170px;width:262px;height:214px}
.lower-zone{left:0;top:378px;width:512px;height:200px;background:var(--white);clip-path:polygon(0 4px,6% 0,12% 6px,19% 2px,26% 7px,33% 1px,40% 5px,47% 2px,54% 7px,61% 1px,68% 6px,75% 2px,82% 7px,89% 1px,95% 5px,100% 2px,100% 100%,0 100%)}
.list{position:absolute;list-style:none;font-size:7.9px}
.list li{position:relative;padding-left:13px;margin-bottom:1px;line-height:1.27}
.list li span{position:absolute;left:0;top:1px;width:9px;height:9px;border-radius:50%;color:var(--white);font-size:6.5px;font-weight:700;text-align:center;line-height:9px}
.list--why li span{background:var(--orange)}
.list--how li span{background:var(--green)}
.forest{left:0;top:558px;width:512px;height:119px;background:linear-gradient(180deg,#3d3a2c,#5b5537 45%,#2e3a22);clip-path:polygon(0 8px,7% 3px,14% 10px,22% 2px,31% 9px,40% 4px,50% 11px,60% 3px,70% 9px,80% 2px,90% 8px,100% 4px,100% 100%,0 100%)}
.quote{left:155px;top:618px;font-family:"Dancing Script",cursive;font-weight:600;font-size:28px;color:var(--white)}
.back-footer{left:0;top:677px;width:512px;height:34px;background:var(--blue);color:#111;font-family:"Montserrat",sans-serif;font-weight:700;font-size:11px}
.back-strip{left:0;top:711px;width:512px;height:13px;background:#111}
</style>
</head>
<body>

<!-- FRONT PAGE -->
<section class="page page--front">
  <div class="brand-dot" style="left:96px;top:14px;width:46px;height:46px"></div>
  <div class="brand-name" style="left:46px;top:64px;font-size:21px;color:var(--blue)">bright meadow</div>
  <div class="abs front-tagline">Stillness, Craft and Venture for Bright Meadow</div>

  <div class="abs title-block">
    <div class="title title--quiet">QUIET</div>
    <div class="title title--path">PATHFINDER</div>
    <div class="title title--course">COURSE</div>
  </div>

  <svg class="abs hero-visual" viewBox="0 0 286 352" role="img" aria-label="Nature photo collage: blue sky with clouds, orange sunset sky and green rolling hills inside a large painted circle">
    <defs>
      <linearGradient id="heroSky" x1="0" y1="0" x2="0" y2="1">
        <stop offset="0" stop-color="#3f9fdc"/>
        <stop offset=".35" stop-color="#bcd9ea"/>
        <stop offset=".55" stop-color="#8fb848"/>
        <stop offset="1" stop-color="#4f8a1e"/>
      </linearGradient>
      <radialGradient id="heroSun" cx=".85" cy=".2" r=".55">
        <stop offset="0" stop-color="#f7b27a"/>
        <stop offset="1" stop-color="#e06a1e" stop-opacity="0"/>
      </radialGradient>
    </defs>
    <circle cx="140" cy="165" r="142" fill="url(#heroSky)"/>
    <circle cx="140" cy="165" r="142" fill="url(#heroSun)"/>
  </svg>

  <div class="abs session-band">
    <div class="session-band__label">Information Session</div>
    <div class="session-band__date">Thursday 18th July 2019 19:30 to 21:00</div>
  </div>

  <h2 class="section-head" style="left:19px;top:332px">Information Session</h2>
  <p class="body-copy" style="left:19px;top:355px;width:475px">The purpose of this Information Session is to give you a real insight into the Quiet Pathfinder Course and how it can help you get the most out of your work and life.</p>

  <h2 class="section-head" style="left:20px;top:387px">Who can come</h2>
  <p class="body-copy" style="left:20px;top:409px;width:475px;text-align:justify">The Information Session is free and whether you come on your own, or with friends or family, you’ll be warmly welcome. It will take place on Thursday the 23rd July 2019, from 19:30 to 21:00, at KOA Coworking. Please get in touch for more info or to book a place.</p>

  <div class="abs facilitator-zone"></div>
  <div class="abs portrait" role="img" aria-label="Portrait photo of the facilitator"></div>
  <div class="abs facilitator-label">Facilitator</div>
  <div class="abs facilitator-name">DR TOMAS RIVERA</div>
  <div class="abs facilitator-role">Visiting Research Fellow, University of Harrowgate</div>
  <p class="abs facilitator-bio">Tomas joined the University of Harrowgate (School of Management) as a Lecturer in Entrepreneurship in 2015. He completed his PhD in Entrepreneurship at Kelvin Business School in 2014. His work received the Lindqvist Doctoral Dissertation Award from the Society of Management Studies. He began his business career as a production engineer (Voltrek), and continued in sales (Norvax). After his MBA, he worked as a strategy consultant at Douro Business School. Originally from Portugal, Tomas enjoys designing and launching new ideas, international communities, mindfulness retreats, and musical improvisation. He nurtures a close connection to Willow Hollow Mindfulness Centre, where he has practiced and volunteered over 9 months. He has a broad experience of sharing the benefits of mindfulness with others.</p>
  <p class="abs facilitator-link">More about the facilitator: <b>www.brightmeadow.io/tomas</b></p>

  <div class="abs footer">
    <div class="footer__contact">
      <div class="icon-disc" style="left:13px;top:5px;width:24px;height:24px">
        <svg viewBox="0 0 24 24" width="24" height="24"><path d="M8 6.5c1-.6 1.8 0 2.3 1l.8 1.7c.3.7 0 1.2-.6 1.6-.4.3-.4.6-.2 1 .6 1 1.3 1.7 2.3 2.3.4.2.7.2 1-.2.4-.6.9-.9 1.6-.6l1.7.8c1 .5 1.6 1.3 1 2.3-.8 1.3-2.4 1.7-4 1-3-1.3-5.2-3.5-6.5-6.5-.7-1.6-.3-3.2 1-4z" fill="#fff"/></svg>
      </div>
      <div class="abs small" style="left:45px;top:3px;color:#fff">For More Information</div>
      <div class="abs" style="left:45px;top:11px;color:#fff;font-weight:700;font-size:16px;font-family:'Montserrat',sans-serif;white-space:nowrap">+34 611 204 395</div>
    </div>
    <div class="footer__booking">
      <div class="abs" style="left:10px;top:6px;font-weight:700;font-size:11.5px;color:#111">INFORMATION &amp; BOOKING:</div>
      <div class="abs" style="left:10px;top:21px;font-size:5.2px;color:#222;white-space:nowrap">Please contact for more information or to book a place</div>
      <svg class="abs" style="left:194px;top:6px" width="8" height="8" viewBox="0 0 10 10"><circle cx="5" cy="5" r="5" fill="#111"/><path d="M5 2.2a2 2 0 0 0-2 2c0 1.5 2 3.6 2 3.6s2-2.1 2-3.6a2 2 0 0 0-2-2z" fill="#fff"/></svg>
      <div class="abs footer-detail" style="left:205px;top:7px">KOA Coworking. C/ Almendro 42. Valencia</div>
      <svg class="abs" style="left:194px;top:19px" width="8" height="8" viewBox="0 0 10 10"><circle cx="5" cy="5" r="5" fill="#111"/><rect x="2.5" y="3.3" width="5" height="3.5" fill="#fff"/><path d="M2.5 3.3 5 5.3 7.5 3.3" stroke="#111" stroke-width=".6" fill="none"/></svg>
      <div class="abs footer-detail" style="left:205px;top:20px">info@brightmeadow.io</div>
    </div>
  </div>
  <div class="abs footer__strip">VIDICALL AND CHATWAVE</div>
</section>

<!-- BACK PAGE -->
<section class="page page--back">
  <div class="abs back-top"></div>
  <div class="brand-dot" style="left:188px;top:14px;width:46px;height:46px"></div>
  <div class="brand-name" style="left:244px;top:14px;font-size:21px;line-height:.98;color:var(--orange)">bright<br>meadow</div>

  <div class="abs back-band">
    <h1>What is Mindful Entrepreneurship</h1>
    <p>Being mindful means being aware and awake. Entrepreneurship is the creation of a new form of organising. Mindful Entrepreneurship is then the process of creating or redesigning your work and life with awareness, in a way that is reflective of you, of your passions and values, thus conducing to a greater sense of fulfilment and happiness.</p>
  </div>

  <div class="abs program-zone"></div>
  <h2 class="abs program-head">The Program</h2>
  <div class="abs program-copy">
    <p><b>The Quiet Pathfinder Course</b> is a <b>4-month long transformative journey</b> designed for people who feel stuck or not entirely satisfied with their work and/or life. It is of benefit for everyone, at any stage.</p>
    <p style="margin-top:9px">The Program consists of a 5-hour workshop each month, with 2-hour weekly peer support meetings. It combines mindfulness techniques, design thinking methodology, and entrepreneurship frameworks.</p>
  </div>

  <svg class="abs cycle" viewBox="0 0 262 214" font-family="Open Sans, sans-serif">
    <g fill="none" stroke-width="5">
      <path d="M157 40 Q180 48 184 62" stroke="#acd037"/>
      <path d="M186 143 Q178 160 160 166" stroke="#33a6d7"/>
      <path d="M82 164 Q64 158 58 143" stroke="#f37122"/>
      <path d="M56 62 Q64 46 82 40" stroke="#8e9296"/>
    </g>
    <g>
      <path d="M180 68 l9 -2 -3 -9z" fill="#acd037"/>
      <path d="M154 170 l10 -7 1 9z" fill="#33a6d7"/>
      <path d="M56 137 l-3 10 9 -2z" fill="#f37122"/>
      <path d="M86 36 l-10 1 5 8z" fill="#8e9296"/>
    </g>
    <g font-size="6.3" font-weight="700" fill="#222" text-anchor="middle">
      <text x="30" y="41">WPS meetings</text>
      <text x="25" y="166">WPS meetings</text>
      <text x="226" y="166">WPS meetings</text>
      <text x="222" y="37">Weekly Peer Support</text>
      <text x="222" y="45">(WPS) meetings</text>
      <text x="222" y="53">(2 hours)</text>
    </g>
    <g text-anchor="middle" fill="#fff">
      <circle cx="120" cy="50" r="40" fill="#fff" opacity=".7"/>
      <circle cx="120" cy="50" r="36" fill="#acd037"/>
      <text x="120" y="38" font-size="7.5">Workshop 1</text>
      <text x="120" y="54" font-family="Oswald, sans-serif" font-size="14" font-weight="600">INSIGHT</text>
      <text x="120" y="65" font-size="7.5">(5 hours)</text>

      <circle cx="188" cy="104" r="40" fill="#fff" opacity=".7"/>
      <circle cx="188" cy="104" r="36" fill="#33a6d7"/>
      <text x="188" y="92" font-size="7.5">Workshop 2</text>
      <text x="188" y="108" font-family="Oswald, sans-serif" font-size="14" font-weight="600">DESIGN</text>
      <text x="188" y="119" font-size="7.5">(5 hours)</text>

      <circle cx="120" cy="164" r="40" fill="#fff" opacity=".7"/>
      <circle cx="120" cy="164" r="36" fill="#f37122"/>
      <text x="120" y="152" font-size="7.5">Workshop 3</text>
      <text x="120" y="168" font-family="Oswald, sans-serif" font-size="14" font-weight="600">EXECUTE</text>
      <text x="120" y="179" font-size="7.5">(5 hours)</text>

      <circle cx="56" cy="104" r="40" fill="#fff" opacity=".7"/>
      <circle cx="56" cy="104" r="36" fill="#b7babe"/>
      <text x="56" y="92" font-size="7.5">Workshop 4</text>
      <text x="56" y="108" font-family="Oswald, sans-serif" font-size="14" font-weight="600">PRESENT</text>
      <text x="56" y="119" font-size="7.5">(5 hours)</text>
    </g>
  </svg>

  <div class="abs lower-zone"></div>
  <h2 class="section-head" style="left:22px;top:394px">Why</h2>
  <p class="body-copy" style="left:22px;top:416px;width:216px;font-size:7.9px">Many people are not satisfied with their work, but they don’t know what to do about it. This Program offers you a safe place to conduct your inner journey with collective support, helping you reflect, design, and (very likely) do something about it. It aims at:</p>
  <ol class="list list--why" style="left:22px;top:482px;width:220px">
    <li><span>1</span>Increasing awareness, clarity and confidence</li>
    <li><span>2</span>Having a deeper <b><i>insight</i></b> on what makes you happier and what you want</li>
    <li><span>3</span>Developing a clear <b><i>design</i></b> integrating your intended work and life</li>
    <li><span>4</span>Start <b><i>executing</i></b> this design</li>
  </ol>

  <h2 class="section-head" style="left:262px;top:394px">How</h2>
  <p class="body-copy" style="left:262px;top:416px;width:232px;font-size:7.9px">This Program differs from existing entrepreneurial programs in many ways:</p>
  <ol class="list list--how" style="left:262px;top:446px;width:234px">
    <li><span>1</span>Uses mindfulness and self analysis to look deeply into yourself</li>
    <li><span>2</span>Design and execution decisions are based on happiness rather than (only) financials</li>
    <li><span>3</span>Holistic and inclusive design process, integrating work and life, and building synergies between your different parts</li>
  </ol>
  <p class="body-copy" style="left:262px;top:522px;width:232px;font-size:7.9px">Format includes: lectures, individual work, group sharing, guided activities, experiential exercises, video, audio, handouts and other resources.</p>

  <div class="abs forest" role="img" aria-label="Photo of a person walking along a forest path between tall trees toward the light"></div>
  <div class="abs quote">“The way out is in”</div>

  <div class="abs back-footer">
    <div class="icon-disc" style="left:26px;top:5px;width:24px;height:24px">
      <svg viewBox="0 0 24 24" width="24" height="24"><path d="M8 6.5c1-.6 1.8 0 2.3 1l.8 1.7c.3.7 0 1.2-.6 1.6-.4.3-.4.6-.2 1 .6 1 1.3 1.7 2.3 2.3.4.2.7.2 1-.2.4-.6.9-.9 1.6-.6l1.7.8c1 .5 1.6 1.3 1 2.3-.8 1.3-2.4 1.7-4 1-3-1.3-5.2-3.5-6.5-6.5-.7-1.6-.3-3.2 1-4z" fill="#fff"/></svg>
    </div>
    <div class="abs" style="left:56px;top:10px;white-space:nowrap">+34 611 204 395 (VidiCall and ChatWave)</div>
    <div class="abs" style="left:311px;top:6px;width:2px;height:22px;background:#111"></div>
    <div class="icon-disc" style="left:326px;top:5px;width:24px;height:24px">
      <svg viewBox="0 0 24 24" width="24" height="24"><rect x="6.5" y="8" width="11" height="8" rx="1" fill="#fff"/><path d="M6.5 8.5 12 12.5l5.5-4" stroke="#111" stroke-width="1.2" fill="none"/></svg>
    </div>
    <div class="abs" style="left:357px;top:10px;white-space:nowrap">info@brightmeadow.io</div>
  </div>
  <div class="abs back-strip"></div>
</section>

</body>
</html>
```